QVR business card

Need a business card for a company that provides instructional design and elearning development services. The website is here: http://quorvane.studio/

I'm attaching a current logo, as well as the old business card design. While I like to keep it clean, the old design is too simplistic for my liking. The only idea I want to reuse from the old design is placing industry jargon on the back of the card, just need a better way to present it. But if you have other ideas for the back--feel free to experiment.

Please use the colors complementary to the color we have on the website. Thank you!

```html
<!DOCTYPE html>
<html lang="en">
<head>
<meta charset="utf-8">
<title>QVR Business Card</title>
<link rel="stylesheet" href="https://fonts.googleapis.com/css2?family=Montserrat:wght@400;500;600;700&family=Roboto:wght@400;500&display=swap">
<style>
  :root {
    --stage: #2b2b2d;
    --teal: #1ea79f;
    --teal-deep: #17958e;
    --gold: #d8c58a;
    --white: #ffffff;
    --ink: #222222;
    --card-shadow: 0 10px 28px rgba(0,0,0,0.45);
  }
  * { margin: 0; padding: 0; box-sizing: border-box; }
  html, body {
    width: 1200px; height: 900px; overflow: hidden;
    background: var(--stage);
  }
  .stage {
    position: relative; width: 1200px; height: 900px;
  }
  .card {
    position: absolute; left: 320px; width: 560px; height: 320px;
    border-radius: 22px; box-shadow: var(--card-shadow); overflow: hidden;
  }
  /* Back side */
  .card--back {
    top: 110px;
    background: linear-gradient(135deg, var(--teal) 0%, var(--teal-deep) 100%);
    display: flex; flex-direction: column; justify-content: center; align-items: center;
    font-family: "Montserrat", Arial, sans-serif; text-align: center;
  }
  .jargon {
    color: var(--white); font-weight: 500; font-size: 25px;
    letter-spacing: 2.5px; line-height: 1.2; text-transform: uppercase;
  }
  .tagline {
    color: var(--gold); font-weight: 700; font-size: 34px;
    letter-spacing: 1.5px; margin: 14px 0 16px; text-transform: uppercase;
  }
  /* Front side */
  .card--front {
    top: 470px; background: var(--white);
  }
  .brand {
    position: absolute; left: 70px; top: 96px;
    display: flex; align-items: center; gap: 14px;
  }
  .brand__mark {
    width: 46px; height: 46px; background: var(--teal); border-radius: 4px;
  }
  .brand__name {
    font-family: "Montserrat", Arial, sans-serif; font-weight: 700;
    font-size: 48px; color: var(--gold); letter-spacing: 0.5px; line-height: 1;
  }
  .contact {
    position: absolute; left: 262px; top: 166px;
    font-family: "Roboto", Arial, sans-serif;
  }
  .contact__name {
    font-family: "Montserrat", Arial, sans-serif; font-weight: 600;
    color: var(--teal); font-size: 19px; letter-spacing: 0.5px;
    text-transform: uppercase; margin-bottom: 8px;
  }
  .contact__row {
    display: flex; align-items: center; gap: 8px;
    font-size: 14px; color: var(--ink); line-height: 1.55;
  }
  .contact__icon { width: 12px; height: 12px; flex: none; }
</style>
</head>
<body>
<main class="stage">
  <section class="card card--back" aria-label="Card back">
    <p class="jargon">Mobile Learning SCORM<br>Instructional Design LMS<br>MOOCs eLearning HTML5</p>
    <h2 class="tagline">How can we help?</h2>
    <p class="jargon">Adult Learning Theory<br>Gamification Classroom<br>xAPI Blended Learning</p>
  </section>

  <section class="card card--front" aria-label="Card front">
    <div class="brand">
      <span class="brand__mark" aria-hidden="true"></span>
      <span class="brand__name">Quorvane</span>
    </div>
    <div class="contact">
      <p class="contact__name">Marcus Delaney</p>
      <p class="contact__row">
        <svg class="contact__icon" viewBox="0 0 12 12" aria-hidden="true"><path d="M2.5 1 L4.5 1 L5.2 3.4 L4 4.3 Q5 6.6 7.7 8 L8.6 6.8 L11 7.5 L11 9.5 Q10.5 11 9 11 Q1 10 1 2.5 Q1 1 2.5 1Z" fill="#1ea79f"/></svg>
        555-204-7731
      </p>
      <p class="contact__row">
        <svg class="contact__icon" viewBox="0 0 12 12" aria-hidden="true"><g fill="none" stroke="#1ea79f" stroke-width="1"><circle cx="6" cy="6" r="5"/><ellipse cx="6" cy="6" rx="2.2" ry="5"/><path d="M1 6 H11 M2 3.5 H10 M2 8.5 H10"/></g></svg>
        www.quorvane.studio
      </p>
      <p class="contact__row">
        <svg class="contact__icon" viewBox="0 0 12 12" aria-hidden="true"><g fill="none" stroke="#1ea79f" stroke-width="1.1"><rect x="1" y="2.5" width="10" height="7" rx="1"/><path d="M1.3 3 L6 6.6 L10.7 3"/></g></svg>
        mdelaney@quorvane.studio
      </p>
    </div>
  </section>
</main>
</body>
</html>
```